Structural Engineering Business Card

Brookvane Drafting does residential house plans for clients in Central Florida. Would like simple but elegant business card that is appropriate for a house plan engineering company. Prefer black business card with black/white them but open to other shades of blue. I uploaded a sample card that I came across that looked good but please come up with your own creative designs.

Contact Information for Business Card

Name, Title, Phone, Email, Address, website

```html
<!DOCTYPE html>
<html lang="en">
<head>
<meta charset="utf-8">
<title>Brookvane Drafting Business Card</title>
<link href="https://fonts.googleapis.com/css2?family=Montserrat:wght@400;500;600;700&display=swap" rel="stylesheet">
<style>
  :root {
    --backdrop: #161616;
    --card: #1f1f1f;
    --card-edge: #2a2a2a;
    --ink: #ffffff;
    --foil: #c9c9c9;
    --muted: #e6e6e6;
  }
  * { margin: 0; padding: 0; box-sizing: border-box; }
  html, body { width: 1200px; height: 900px; overflow: hidden; }
  body {
    background: var(--backdrop);
    font-family: "Montserrat", sans-serif;
    color: var(--ink);
    position: relative;
  }
  .card {
    position: absolute;
    left: 290px;
    width: 620px;
    height: 354px;
    background: var(--card);
    border: 1px solid var(--card-edge);
    box-shadow: 0 14px 30px rgba(0,0,0,0.55);
  }
  .card--front { top: 72px; }
  .card--back { top: 474px; }

  .wordmark {
    display: flex;
    align-items: center;
    gap: 12px;
    font-weight: 700;
    letter-spacing: 0.5px;
    white-space: nowrap;
  }
  .wordmark__square {
    width: 18px; height: 18px;
    background: currentColor;
    flex: none;
  }
  .card--front .wordmark {
    position: absolute;
    left: 50%; top: 50%;
    transform: translate(-50%, -50%);
    font-size: 38px;
    color: var(--foil);
  }
  .card--back .wordmark {
    position: absolute;
    left: 40px; top: 50%;
    transform: translateY(-50%);
    font-size: 24px;
    color: var(--ink);
  }
  .divider {
    position: absolute;
    left: 345px; top: 72px;
    width: 1.5px; height: 210px;
    background: var(--ink);
  }
  .contact {
    position: absolute;
    left: 372px; top: 80px;
    color: var(--muted);
  }
  .contact__name {
    font-size: 19px; font-weight: 600; letter-spacing: 1px;
    color: var(--ink); text-transform: uppercase;
  }
  .contact__title {
    font-size: 12px; font-weight: 500; letter-spacing: 1.5px;
    text-transform: uppercase; margin-bottom: 12px;
  }
  .contact__address { font-size: 13.5px; line-height: 1.35; margin-bottom: 8px; }
  .contact__line {
    display: flex; align-items: center; gap: 6px;
    font-size: 13px; line-height: 1.55;
  }
  .contact__line svg { width: 11px; height: 11px; flex: none; }
</style>
</head>
<body>
  <section class="card card--front" aria-label="Card front">
    <div class="wordmark"><span class="wordmark__square"></span>Brookvane Drafting</div>
  </section>

  <section class="card card--back" aria-label="Card back">
    <div class="wordmark"><span class="wordmark__square"></span>Brookvane Drafting</div>
    <div class="divider"></div>
    <div class="contact">
      <p class="contact__name">Daniel Reyes</p>
      <p class="contact__title">Director</p>
      <p class="contact__address">418 Harlow Lane<br>Ocala, FL 34471</p>
      <p class="contact__line">
        <svg viewBox="0 0 24 24" fill="none" stroke="currentColor" stroke-width="2.4"><path d="M5 3h4l2 5-3 2a12 12 0 0 0 6 6l2-3 5 2v4a2 2 0 0 1-2 2A17 17 0 0 1 3 5a2 2 0 0 1 2-2z"/></svg>
        352.555.0148
      </p>
      <p class="contact__line">
        <svg viewBox="0 0 24 24" fill="none" stroke="currentColor" stroke-width="2.4"><rect x="2" y="5" width="20" height="14"/><path d="M2 5l10 8 10-8"/></svg>
        info@brookvanedrafting.com
      </p>
      <p class="contact__line">
        <svg viewBox="0 0 24 24" fill="none" stroke="currentColor" stroke-width="2.2"><circle cx="12" cy="12" r="10"/><path d="M2 12h20M12 2c3 3 3 17 0 20M12 2c-3 3-3 17 0 20"/></svg>
        www.brookvanedrafting.com
      </p>
    </div>
  </section>
</body>
</html>
```